Wall art for an Investments Lab at a college

Wall art for inside a new investments lab. A photo of the lab is attached. The wall art will go on the wall in the back right (pictured). It is currently white and the adjacent walls are white. The accent wall in the room is blue (summer nights). A copy of our color palette for environmental design is also attached. The tag line should be INVESTING IN THE FUTURE.

Target Market(s)

College students

Industry/Entity Type

Finance

Requirements
Must have
• Incorporate colors from palette

```html
<!DOCTYPE html>
<html lang="en">
<head>
<meta charset="utf-8">
<title>Investing in the Future — Wall Art</title>
<link href="https://fonts.googleapis.com/css2?family=Big+Shoulders+Display:wght@500&display=swap" rel="stylesheet">
<style>
  :root {
    --wall-light: #54829c;
    --wall-mid: #46748f;
    --wall-deep: #3d6c8b;
    --ink: #ffffff;
    --area-top: rgba(255, 255, 255, 0.2);
    --area-bottom: rgba(255, 255, 255, 0.04);
  }
  html, body {
    margin: 0;
    padding: 0;
    width: 1200px;
    height: 1033px;
    overflow: hidden;
  }
  .wall-art {
    display: block;
    width: 1200px;
    height: 1033px;
  }
  .tagline, .brand-name {
    font-family: "Big Shoulders Display", "Arial Narrow", sans-serif;
    font-weight: 500;
    font-size: 56px;
    fill: none;
    stroke: var(--ink);
    stroke-width: 1.6px;
    letter-spacing: 1px;
  }
  .axis { stroke: var(--ink); stroke-width: 3; fill: none; }
  .tick { stroke: var(--ink); stroke-width: 1.6; }
  .trend-line { stroke: var(--ink); stroke-width: 2; fill: none; }
  .trend-area { fill: url(#areaFade); stroke: none; }
  .drop-line { stroke: var(--ink); stroke-width: 1.4; stroke-dasharray: 5 4; }
  .data-point { fill: var(--ink); }
  .brand-mark { fill: none; stroke: var(--ink); stroke-width: 2.4; }
</style>
</head>
<body>
<svg class="wall-art" viewBox="0 0 1200 1033" xmlns="http://www.w3.org/2000/svg">
  <defs>
    <linearGradient id="wallTone" x1="0" y1="0" x2="1" y2="0">
      <stop offset="0" stop-color="var(--wall-light)"/>
      <stop offset="0.5" stop-color="var(--wall-mid)"/>
      <stop offset="1" stop-color="var(--wall-deep)"/>
    </linearGradient>
    <linearGradient id="areaFade" x1="0" y1="0" x2="0" y2="1">
      <stop offset="0" stop-color="var(--area-top)"/>
      <stop offset="1" stop-color="var(--area-bottom)"/>
    </linearGradient>
  </defs>

  <rect class="background" width="1200" height="1033" fill="url(#wallTone)"/>

  <!-- growth chart -->
  <g class="chart">
    <polygon class="trend-area" points="26,764 222,900 416,854 611,436 804,564 998,509 1192,131 1200,131 1200,956 26,956"/>

    <g class="drop-lines">
      <line class="drop-line" x1="222" y1="900" x2="222" y2="956"/>
      <line class="drop-line" x1="416" y1="854" x2="416" y2="956"/>
      <line class="drop-line" x1="611" y1="436" x2="611" y2="956"/>
      <line class="drop-line" x1="804" y1="564" x2="804" y2="956"/>
      <line class="drop-line" x1="998" y1="509" x2="998" y2="956"/>
      <line class="drop-line" x1="1192" y1="131" x2="1192" y2="956"/>
    </g>

    <polyline class="trend-line" points="26,764 222,900 416,854 611,436 804,564 998,509 1192,131 1200,116"/>

    <g class="data-points">
      <ellipse class="data-point" cx="222" cy="900" rx="8" ry="9"/>
      <ellipse class="data-point" cx="416" cy="854" rx="8" ry="9"/>
      <ellipse class="data-point" cx="611" cy="436" rx="8" ry="9"/>
      <ellipse class="data-point" cx="804" cy="564" rx="8" ry="9"/>
      <ellipse class="data-point" cx="998" cy="509" rx="8" ry="9"/>
      <ellipse class="data-point" cx="1192" cy="131" rx="8" ry="9"/>
    </g>

    <g class="y-ticks">
      <line class="tick" x1="26" y1="8" x2="36" y2="8"/>
      <line class="tick" x1="26" y1="66" x2="36" y2="66"/>
      <line class="tick" x1="26" y1="125" x2="36" y2="125"/>
      <line class="tick" x1="26" y1="183" x2="36" y2="183"/>
      <line class="tick" x1="26" y1="241" x2="36" y2="241"/>
      <line class="tick" x1="26" y1="300" x2="36" y2="300"/>
      <line class="tick" x1="26" y1="358" x2="36" y2="358"/>
      <line class="tick" x1="26" y1="416" x2="36" y2="416"/>
      <line class="tick" x1="26" y1="475" x2="36" y2="475"/>
      <line class="tick" x1="26" y1="533" x2="36" y2="533"/>
      <line class="tick" x1="26" y1="591" x2="36" y2="591"/>
      <line class="tick" x1="26" y1="650" x2="36" y2="650"/>
      <line class="tick" x1="26" y1="708" x2="36" y2="708"/>
      <line class="tick" x1="26" y1="766" x2="36" y2="766"/>
      <line class="tick" x1="26" y1="825" x2="36" y2="825"/>
      <line class="tick" x1="26" y1="883" x2="36" y2="883"/>
      <line class="tick" x1="26" y1="941" x2="36" y2="941"/>
    </g>

    <g class="x-ticks">
      <line class="tick" x1="62" y1="946" x2="62" y2="956"/>
      <line class="tick" x1="109" y1="946" x2="109" y2="956"/>
      <line class="tick" x1="155" y1="946" x2="155" y2="956"/>
      <line class="tick" x1="201" y1="946" x2="201" y2="956"/>
      <line class="tick" x1="248" y1="946" x2="248" y2="956"/>
      <line class="tick" x1="294" y1="946" x2="294" y2="956"/>
      <line class="tick" x1="341" y1="946" x2="341" y2="956"/>
      <line class="tick" x1="387" y1="946" x2="387" y2="956"/>
      <line class="tick" x1="434" y1="946" x2="434" y2="956"/>
      <line class="tick" x1="480" y1="946" x2="480" y2="956"/>
      <line class="tick" x1="526" y1="946" x2="526" y2="956"/>
      <line class="tick" x1="573" y1="946" x2="573" y2="956"/>
      <line class="tick" x1="619" y1="946" x2="619" y2="956"/>
      <line class="tick" x1="666" y1="946" x2="666" y2="956"/>
      <line class="tick" x1="712" y1="946" x2="712" y2="956"/>
      <line class="tick" x1="759" y1="946" x2="759" y2="956"/>
      <line class="tick" x1="805" y1="946" x2="805" y2="956"/>
      <line class="tick" x1="851" y1="946" x2="851" y2="956"/>
      <line class="tick" x1="898" y1="946" x2="898" y2="956"/>
      <line class="tick" x1="944" y1="946" x2="944" y2="956"/>
      <line class="tick" x1="991" y1="946" x2="991" y2="956"/>
      <line class="tick" x1="1037" y1="946" x2="1037" y2="956"/>
      <line class="tick" x1="1084" y1="946" x2="1084" y2="956"/>
      <line class="tick" x1="1130" y1="946" x2="1130" y2="956"/>
      <line class="tick" x1="1176" y1="946" x2="1176" y2="956"/>
    </g>

    <polyline class="axis" points="26,0 26,956 1200,956"/>
  </g>

  <!-- title lockup -->
  <g class="title-lockup">
    <circle class="brand-mark" cx="222" cy="301" r="14"/>
    <text class="brand-name" x="244" y="321" textLength="84" lengthAdjust="spacingAndGlyphs">ARDEN</text>
    <text class="tagline" x="342" y="321" textLength="576" lengthAdjust="spacingAndGlyphs">INVESTING IN THE FUTURE</text>
  </g>
</svg>
</body>
</html>
```